Fernhale Business Card Design

We are looking for a fresh business card design for our new logo. We would like a business card that is unique but friendly. We are in the window coverings business offering blinds, shutters and shades for homes.

Target Market(s)

Targeting the end-consumer

Industry/Entity Type

Business

Requirements
Must have
• Must have a dedicates space for a photo of our sales person. Must contain our new logo (attached).

```html
<!DOCTYPE html>
<html lang="en">
<head>
<meta charset="utf-8">
<title>Fernhale Business Card</title>
<link href="https://fonts.googleapis.com/css2?family=Roboto:wght@400;500&family=Roboto+Condensed:wght@500&display=swap" rel="stylesheet">
<style>
  :root {
    --leaf-green: #7dbb3b;
    --paper: #f1f1f1;
    --stem-grey: #7a7a7b;
    --backdrop: #e4e2de;
    --ink-white: #ffffff;
  }
  * { margin: 0; padding: 0; box-sizing: border-box; }
  html, body { width: 1200px; height: 960px; overflow: hidden; }
  body {
    position: relative;
    background: var(--backdrop);
    font-family: "Roboto", Arial, sans-serif;
  }
  .card {
    position: absolute;
    width: 600px;
    height: 343px;
    overflow: hidden;
    box-shadow: 0 2px 6px rgba(0,0,0,0.25);
  }
  .card-front { left: 314px; top: 113px; background: var(--paper); }
  .card-back { left: 311px; top: 472px; height: 342px; background: var(--leaf-green); }

  .front-panel {
    position: absolute; left: 0; top: 0;
    width: 289px; height: 100%;
    background: var(--leaf-green);
  }
  .divider-band {
    position: absolute; left: 289px; top: 0;
    width: 16px; height: 100%;
    background: var(--stem-grey);
  }
  .accent-slot {
    position: absolute; left: 289px; top: 0;
    width: 84px; height: 64px;
    background: var(--stem-grey);
  }
  .person-name {
    position: absolute; left: 39px; top: 49px;
    font-family: "Roboto Condensed", "Arial Narrow", sans-serif;
    font-weight: 500; font-size: 21px;
    color: var(--ink-white);
  }
  .person-role {
    position: absolute; left: 39px; top: 75px;
    font-size: 14.5px; color: var(--ink-white);
  }
  .address {
    position: absolute; left: 40px; top: 159px;
    font-size: 14px; line-height: 18px; color: var(--ink-white);
  }
  .contact-list {
    position: absolute; left: 40px; top: 205px;
    list-style: none;
  }
  .contact-list li {
    display: flex; align-items: center;
    height: 19px;
    font-size: 14px; color: var(--ink-white);
  }
  .contact-list svg { width: 14px; height: 14px; margin-right: 9px; flex: none; }

  .brand {
    position: absolute;
    display: flex; align-items: center;
  }
  .brand-mark { border-radius: 4px; flex: none; }
  .brand-name { font-family: "Roboto", Arial, sans-serif; font-weight: 400; }
  .card-front .brand { left: 344px; top: 243px; }
  .card-front .brand-mark { width: 48px; height: 48px; border: 3px solid var(--stem-grey); }
  .card-front .brand-name { margin-left: 12px; font-size: 34px; color: var(--stem-grey); }

  .photo-slot {
    position: absolute; left: 2px; top: 33px;
    width: 274px; height: 309px;
    background: var(--paper);
    border-radius: 60px 60px 0 0;
  }
  .card-back .brand { left: 317px; top: 232px; }
  .card-back .brand-mark { width: 50px; height: 50px; border: 3px solid var(--ink-white); }
  .card-back .brand-name { margin-left: 16px; font-size: 38px; color: var(--ink-white); }
  .web-line {
    position: absolute; left: 317px; top: 294px;
    font-size: 13px; letter-spacing: 8.6px;
    color: var(--ink-white);
  }
</style>
</head>
<body>

<section class="card card-front">
  <div class="front-panel"></div>
  <div class="divider-band"></div>
  <div class="accent-slot" role="img" aria-label="Decorative leaf accent at the top of the divider"></div>

  <h1 class="person-name">MARA ELLISON</h1>
  <p class="person-role">CEO/FOUNDER</p>

  <p class="address">412 Larkspur Way<br>Juneau, Alaska 39821</p>

  <ul class="contact-list">
    <li><svg viewBox="0 0 14 14"><path d="M3 1 L5 1 L6 4 L4.5 5.5 Q6 8.5 8.5 9.5 L10 8 L13 9 L13 11 Q12 13 10 13 Q2 11 1 3 Q1 1 3 1 Z" fill="#fff"/></svg>615 204 7731</li>
    <li><svg viewBox="0 0 14 14"><rect x="3.5" y="0.5" width="7" height="13" rx="1" fill="none" stroke="#fff"/><rect x="5" y="2" width="4" height="8" fill="#fff"/></svg>615 882 1046</li>
    <li><svg viewBox="0 0 14 14"><rect x="3" y="1" width="8" height="4" fill="#fff"/><rect x="0.5" y="5" width="13" height="6" rx="1" fill="#fff"/><rect x="3" y="9" width="8" height="4" fill="#fff" stroke="#7dbb3b" stroke-width="0.8"/></svg>615 390 5528</li>
    <li><svg viewBox="0 0 14 14"><rect x="0.5" y="3" width="13" height="8.5" fill="#fff"/><path d="M0.5 3 L7 8 L13.5 3" fill="none" stroke="#7dbb3b" stroke-width="1"/></svg>name@fernhale.com</li>
    <li><svg viewBox="0 0 14 14"><circle cx="7" cy="7" r="6" fill="#fff"/><path d="M4 5 Q6 4 7 6 Q6 8 8 9 M9 3 Q11 5 10 7" fill="none" stroke="#7dbb3b" stroke-width="1.2"/></svg>www.fernhale.com</li>
  </ul>

  <div class="brand">
    <span class="brand-mark"></span>
    <span class="brand-name">Fernhale</span>
  </div>
</section>

<section class="card card-back">
  <div class="photo-slot" role="img" aria-label="Photo of the sales person, head and shoulders"></div>
  <div class="brand">
    <span class="brand-mark"></span>
    <span class="brand-name">Fernhale</span>
  </div>
  <p class="web-line">www.fernhale.com</p>
</section>

</body>
</html>
```